NZ First of it's kind solutions directory and marketplace for busy Mums needs a business card design

We need a business card design for our new nationwide business in NZ (long term plans to go global). We provide solutions to the everyday challenges that busy Mums face by connecting them with quality communities and suppliers of carefully selected, relevant products and services. We sell direct via our online marketplace. The final design should communicate our values of inclusivity, quality and smart solutions. Colours should incorporate our logo colour palette of #477077 and #6ba8b2. Our website is at https://www.brightnestmums.example

Target Market(s)

busy Mums, Age 28 – 50, female, income over $100K, location main centres NZ primarily but NZ wide. Is likely juggling work or career with a young family. Probably had hobbies which have fallen by the wayside.
-Wants to succeed in her chosen career without compromising on family life
-to successfully juggle her career without feeling like she is compromising her children
- Is time poor, something always has to give and it’s generally her health (she’ll stay up late, get stressed)
- probably ex corporate or professional career. Has discretional income

Industry/Entity Type

Business

Contact Information for Business Card

Lena Forbisher, Founder, BrightNestMums.example (Strapline Tap; Gather; Sorted), 47 Kowhai Terrace, Ellerslie, Auckland 1051, New Zealand. Mob: 021 483 517 Ph: +64 (0)9 571 4860

Font styles to use
Other font styles liked:
• Raleway, and/or Architects Daughter

Colors
00a990
33b8a4
86cfc6
cfeae6

Requirements
Must have
• the above details, streamline. the logo and colours associated with those logos
Should not have
• foil or metallic colours

```html
<!DOCTYPE html>
<html lang="en">
<head>
<meta charset="utf-8">
<title>BrightNestMums – Business Card</title>
<link rel="stylesheet" href="https://fonts.googleapis.com/css2?family=Roboto+Condensed:ital,wght@0,400;0,700;1,400&display=swap">
<style>
  :root {
    --teal-deep: #477077;
    --teal-dark: #3b5a62;
    --teal-light: #6ba8b2;
    --ink: #3f4446;
    --card: #f7f7f7;
    --backdrop: #e4e4e4;
  }
  * { box-sizing: border-box; margin: 0; padding: 0; }
  html, body { width: 1200px; height: 576px; overflow: hidden; }
  body {
    background: var(--backdrop);
    font-family: "Roboto Condensed", sans-serif;
    position: relative;
  }
  .card {
    position: absolute;
    top: 138px;
    width: 484px;
    height: 294px;
    background: var(--card);
    border-radius: 14px;
    overflow: hidden;
    box-shadow: 0 3px 6px rgba(0,0,0,0.22);
  }
  .card--front { left: 82px; }
  .card--back { left: 602px; }

  .wordmark {
    position: absolute;
    font-family: "Roboto Condensed", sans-serif;
    font-weight: 700;
    color: var(--teal-deep);
    white-space: nowrap;
  }
  .strapline {
    position: absolute;
    font-size: 9px;
    letter-spacing: 3.2px;
    color: var(--ink);
    white-space: nowrap;
  }
  .strapline .divider { color: var(--teal-light); padding: 0 4px; }
  .brand-dot {
    position: absolute;
    border-radius: 50%;
    background: var(--teal-dark);
  }

  /* front */
  .card--front .brand-dot { left: 32px; top: 127px; width: 30px; height: 30px; }
  .card--front .wordmark { left: 70px; top: 122px; font-size: 30px; }
  .card--front .strapline { left: 72px; top: 168px; }
  .front-disc {
    position: absolute;
    left: 284px; top: 106px;
    width: 200px; height: 200px;
    border-radius: 50%;
    background: var(--teal-dark);
  }

  /* back */
  .card--back .brand-dot { left: 118px; top: 102px; width: 32px; height: 32px; }
  .card--back .wordmark { left: 40px; top: 162px; width: 186px; text-align: center; font-size: 28px; }
  .card--back .strapline { left: 40px; top: 204px; width: 186px; text-align: center; letter-spacing: 2.6px; }

  .contact { position: absolute; left: 264px; top: 56px; color: var(--ink); }
  .contact__name { font-size: 21px; font-weight: 700; color: var(--teal-deep); line-height: 1.1; }
  .contact__role { font-size: 12.5px; font-style: italic; margin-top: 2px; }
  .contact__address { font-size: 12.5px; line-height: 18px; margin-top: 18px; }
  .contact__lines { list-style: none; margin-top: 12px; }
  .contact__lines li { font-size: 12.5px; line-height: 18.4px; display: flex; align-items: center; gap: 8px; }
  .contact__lines svg { width: 10px; height: 10px; fill: var(--teal-deep); flex: none; }
</style>
</head>
<body>

<section class="card card--front">
  <span class="brand-dot"></span>
  <span class="wordmark">BrightNestMums</span>
  <p class="strapline">TAP<span class="divider">|</span>GATHER<span class="divider">|</span>SORTED</p>
  <span class="front-disc"></span>
</section>

<section class="card card--back">
  <span class="brand-dot"></span>
  <span class="wordmark">BrightNestMums</span>
  <p class="strapline">TAP<span class="divider">|</span>GATHER<span class="divider">|</span>SORTED</p>

  <div class="contact">
    <h1 class="contact__name">Lena Forbisher</h1>
    <p class="contact__role">Founder</p>
    <p class="contact__address">47 Kowhai Terrace, Ellerslie,<br>Auckland 1051, New Zealand</p>
    <ul class="contact__lines">
      <li><svg viewBox="0 0 10 10"><rect x="2.5" y="0" width="5" height="10" rx="1"/></svg>021 483 517</li>
      <li><svg viewBox="0 0 10 10"><path d="M1 3 Q5 0 9 3 L8 4.5 L6.5 3.5 L3.5 3.5 L2 4.5 Z M2 5 H8 V9 H2 Z"/></svg>+64 (0)9 571 4860</li>
      <li><svg viewBox="0 0 10 10"><circle cx="5" cy="5" r="4.5" fill="none" stroke="#477077" stroke-width="1"/><path d="M0.5 5 H9.5 M5 0.5 V9.5" stroke="#477077" stroke-width="0.8"/></svg>www.BrightNestMums.example</li>
      <li><svg viewBox="0 0 10 10"><path d="M0 2 H10 V8 H0 Z M0 2 L5 5.5 L10 2" fill="#477077" stroke="#f7f7f7" stroke-width="0.6"/></svg>lena@brightnestmums.example</li>
    </ul>
  </div>
</section>

</body>
</html>
```